Pet store web design

I would like to redesign my current online store (http://furrowlanemart.com)
I'm looking for a clean, modern design. Any ideas are welcome..

Industry/Entity Type

Pet

Number of Pages Required

3 page

```html
<!DOCTYPE html>
<html lang="en">
<head>
<meta charset="utf-8">
<title>Furrow Lane Mart – Pet Store</title>
<link href="https://fonts.googleapis.com/css2?family=Open+Sans:wght@400;600;700;800&display=swap" rel="stylesheet">
<style>
:root{
  --orange:#f7941d;
  --orange-dark:#e0771a;
  --topbar:#3a3a3a;
  --ink:#333;
  --muted:#888;
  --line:#e2e2e2;
  --hero:#ececec;
  --blue:#1d86c7;
  --sky:#2bb5e6;
  --green:#8cc63f;
  --footer:#3b2e22;
  --footer-text:#cfc6bb;
  --bottom:#c9a52b;
  --white:#fff;
}
*{box-sizing:border-box;margin:0;padding:0}
html,body{width:686px;height:1200px;overflow:hidden}
body{font-family:"Open Sans",Arial,sans-serif;color:var(--ink);background:var(--white);font-size:8px}
.topbar{height:18px;background:var(--topbar);color:#ddd;display:flex;align-items:center;justify-content:space-between;padding:0 40px;font-size:6.5px}
.topbar .social{display:flex;align-items:center;gap:3px}
.dot-ico{width:9px;height:9px;border-radius:2px;background:#777;display:inline-block}
.topbar .account span{margin-left:10px}
.header{height:68px;display:flex;align-items:center;justify-content:space-between;padding:0 40px}
.logo{display:flex;align-items:center;gap:6px}
.logo .mark{width:14px;height:14px;border-radius:50%;background:var(--orange)}
.logo .name{font-weight:800;font-size:15px;color:var(--orange)}
.search{display:flex;width:150px;height:18px;border:1px solid var(--line)}
.search span{flex:1;font-size:6.5px;color:#aaa;padding:4px 6px}
.search i{width:20px;background:var(--orange)}
.cart{display:flex;align-items:center;gap:6px;font-size:6.5px;line-height:1.3}
.cart b{display:block;font-size:7px}
.nav{height:20px;background:var(--orange);display:flex;padding:0 40px}
.nav a{flex:1;text-align:center;color:var(--white);font-weight:700;font-size:7px;line-height:20px;text-decoration:none}
.nav a.active{background:var(--orange-dark)}
.hero{position:relative;height:270px;margin-top:6px;background:linear-gradient(100deg,#f4f4f4 0%,var(--hero) 60%,#dedede 100%);overflow:hidden}
.hero .photo{position:absolute;left:30px;top:20px;width:310px;height:225px;background:linear-gradient(135deg,#d9c1a0,#c0392b 55%,#f1a7c4);border-radius:4px}
.hero .copy{position:absolute;left:390px;top:80px;width:240px}
.hero h1{font-size:24px;font-weight:800;color:var(--ink);letter-spacing:.5px}
.hero p{font-size:10px;color:#555;margin-top:4px;line-height:1.35}
.hero .cta{display:inline-block;margin-top:8px;font-weight:700;font-size:8px;color:var(--orange)}
.arrow{position:absolute;top:120px;width:18px;height:18px;border-radius:50%;background:rgba(0,0,0,.25)}
.arrow.l{left:8px}.arrow.r{right:8px}
.dots{position:absolute;bottom:10px;left:50%;transform:translateX(-50%);display:flex;gap:4px}
.dots i{width:5px;height:5px;border-radius:50%;background:#bbb}
.dots i.on{background:var(--orange)}
.promos{display:flex;height:140px;margin-top:10px}
.promo{flex:1;position:relative;color:var(--white);padding:10px 12px;overflow:hidden}
.promo h2{font-size:12px;font-weight:800;position:relative;z-index:1}
.promo p{font-size:6.5px;margin-top:3px;width:100px;line-height:1.4;position:relative;z-index:1}
.promo .pic{position:absolute;right:8px;bottom:0;width:110px;height:95px;border-radius:4px 4px 0 0}
.promo.boss{background:var(--blue)}.promo.boss .pic{background:linear-gradient(#2a3f6b,#16284a)}
.promo.fall{background:var(--orange)}.promo.fall .pic{background:linear-gradient(#6b5a48,#2d241c)}
.promo.fast{background:var(--sky)}.promo.fast .pic{background:linear-gradient(#d8b88a,#8a6a40)}
.products{padding-top:16px;text-align:center;position:relative;height:260px}
.products h3{font-size:13px;font-weight:800}
.products .rule{width:606px;height:1px;background:var(--line);margin:6px auto 0}
.tabs{display:flex;justify-content:center;gap:2px;margin-top:8px}
.tabs span{font-size:6px;padding:4px 12px;border:1px solid var(--line);color:var(--muted)}
.tabs span.on{background:var(--orange);color:var(--white);border-color:var(--orange)}
.cards{display:flex;gap:12px;width:606px;margin:16px auto 0}
.card{flex:1;border:1px solid var(--line);text-align:left;padding:6px}
.card .pic{height:80px;background:linear-gradient(#f3f3f3,#e2e2e2);border-radius:2px}
.card .name{font-size:6.5px;font-weight:700;margin-top:8px}
.card .price{font-size:7px;color:var(--orange);font-weight:700;margin-top:2px}
.card .row{display:flex;justify-content:space-between;align-items:center;margin-top:6px}
.card .btn{background:var(--orange);color:var(--white);font-size:5.5px;font-weight:700;padding:3px 5px}
.stars{color:var(--orange);font-size:7px;letter-spacing:1px}
.products .arrow{top:155px;background:#ccc;width:12px;height:12px}
.products .arrow.l{left:18px}.products .arrow.r{right:18px}
.newsletter{height:105px;background:var(--green);position:relative;padding:22px 40px;color:var(--white);margin-top:10px}
.newsletter h4{font-size:15px;font-weight:800}
.newsletter p{font-size:7px;margin-top:2px}
.newsletter p b{color:#f4e04d}
.signup{display:flex;margin-top:10px}
.signup span{width:180px;height:18px;background:var(--white);color:#aaa;font-size:6.5px;padding:4px 6px}
.signup b{background:var(--orange);font-size:7px;padding:4px 10px}
.newsletter .pic{position:absolute;right:60px;bottom:0;width:140px;height:120px;background:linear-gradient(#e94e3a,#f6b26b);border-radius:60px 60px 0 0}
.features{display:flex;height:90px;padding:20px 40px 0}
.feature{flex:1;display:flex;gap:8px;align-items:flex-start}
.feature .ico{width:30px;height:30px;border-radius:50%;background:var(--orange);display:flex;align-items:center;justify-content:center;flex:none}
.feature h5{font-size:9px;font-weight:800}
.feature small{display:block;font-size:6px;color:var(--muted)}
.feature em{display:block;font-style:normal;font-size:5.5px;color:var(--orange);font-weight:700;margin-top:4px}
.footer{height:152px;background:var(--footer);color:var(--footer-text);display:flex;padding:20px 40px;gap:20px;font-size:6.5px;line-height:1.6}
.footer .about{width:130px}
.footer .about .name{font-size:12px}
.footer .about p{margin-top:6px}
.cards-pay{display:flex;gap:3px;margin-top:6px}
.cards-pay i{width:16px;height:10px;border-radius:2px;background:#8a7b6a}
.footer .col{flex:1}
.footer h6{font-size:7.5px;color:var(--white);font-weight:700;margin-bottom:4px}
.footer .contact div{display:flex;gap:5px;align-items:flex-start}
.bottombar{height:20px;background:var(--bottom);display:flex;align-items:center;justify-content:space-between;padding:0 40px;color:var(--white);font-size:6px}
.bottombar .social{display:flex;gap:3px}
.bottombar .dot-ico{background:rgba(255,255,255,.6)}
</style>
</head>
<body>
<div class="topbar">
  <div class="social">Follow us on <i class="dot-ico"></i><i class="dot-ico"></i><i class="dot-ico"></i><i class="dot-ico"></i></div>
  <div class="account"><span>My Account</span><span>Checkout</span><span>My Wishlist</span><span>Login</span><span>Register</span></div>
</div>

<header class="header">
  <div class="logo"><span class="mark"></span><span class="name">Furrow Lane Mart</span></div>
  <div class="search"><span>Search</span><i></i></div>
  <div class="cart">
    <svg width="16" height="14" viewBox="0 0 16 14"><path d="M1 1h3l2 8h8l1.5-6H5" fill="none" stroke="#f7941d" stroke-width="1.5"/><circle cx="7" cy="12" r="1.3" fill="#f7941d"/><circle cx="13" cy="12" r="1.3" fill="#f7941d"/></svg>
    <div><b>My Cart</b>0 item(s) - $0.00</div>
  </div>
</header>

<nav class="nav">
  <a class="active">HOME</a><a>DOG</a><a>CAT</a><a>FISH</a><a>BIRD</a><a>SMALL PET</a>
</nav>

<section class="hero">
  <div class="photo" role="img" aria-label="Three small dogs wearing colourful sweaters"></div>
  <div class="copy">
    <h1>FURROW LANE MART</h1>
    <p>We've got it all, for the big the medium and the small</p>
    <span class="cta">SHOP THE COLLECTION ›</span>
  </div>
  <span class="arrow l"></span><span class="arrow r"></span>
  <div class="dots"><i class="on"></i><i></i><i></i></div>
</section>

<section class="promos">
  <div class="promo boss"><h2>SHOW EM WHO'S BOSS!</h2><p>Rugged Collars &amp; Leashes, Limited Stock Available</p><div class="pic" role="img" aria-label="Dog in a dark police-style jacket"></div></div>
  <div class="promo fall"><h2>FALL / WINTER</h2><p>Keep Your Pet Warm with Our Latest Knits</p><div class="pic" role="img" aria-label="Dog in a striped winter sweater"></div></div>
  <div class="promo fast"><h2>TOO FAST FOR HUMAN EYE</h2><p>Racing Harnesses for Speedy Dogs</p><div class="pic" role="img" aria-label="Dog running across grass"></div></div>
</section>

<section class="products">
  <h3>OUR PRODUCTS</h3>
  <div class="rule"></div>
  <div class="tabs"><span class="on">ALL</span><span>MOST POPULAR</span><span>TOP RATED</span><span>FEATURED</span><span>NEW</span></div>
  <div class="cards">
    <div class="card"><div class="pic" role="img" aria-label="Dog wearing a chef costume"></div><div class="name">CHEF DOG COSTUME - LARGE</div><div class="price">$30.00</div><div class="row"><span class="btn">ADD TO CART</span><span class="stars">★★★★★</span></div></div>
    <div class="card"><div class="pic" role="img" aria-label="Dog wearing a green Christmas tree shirt"></div><div class="name">DOG CHRISTMAS TREE SHIRT</div><div class="price">$30.00</div><div class="row"><span class="btn">ADD TO CART</span><span class="stars">★★★★★</span></div></div>
    <div class="card"><div class="pic" role="img" aria-label="Round suede pet nest bed"></div><div class="name">NEST BED - LANDSCAPE SUEDE</div><div class="price">$200.00</div><div class="row"><span class="btn">ADD TO CART</span><span class="stars">★★★★★</span></div></div>
    <div class="card"><div class="pic" role="img" aria-label="Artificial turf potty pad"></div><div class="name">TRIPLE TURF - LARGE</div><div class="price">$16.00</div><div class="row"><span class="btn">ADD TO CART</span><span class="stars">★★★★★</span></div></div>
  </div>
  <span class="arrow l"></span><span class="arrow r"></span>
</section>

<section class="newsletter">
  <h4>30 NEW PRODUCTS EVERY MONTH</h4>
  <p>KEEP UP TO DATE ON THE LATEST FROM FURROW LANE MART <b>WE LOVE PETS</b></p>
  <div class="signup"><span>Enter email address</span><b>SIGN IN</b></div>
  <div class="pic" role="img" aria-label="Dog wearing sunglasses"></div>
</section>

<section class="features">
  <div class="feature"><span class="ico"><svg width="16" height="12" viewBox="0 0 16 12"><path d="M1 2h9v6H1zM10 4h3l2 2v2h-5z" fill="#fff"/><circle cx="4" cy="10" r="1.5" fill="#fff"/><circle cx="12" cy="10" r="1.5" fill="#fff"/></svg></span><div><h5>DELIVERY</h5><small>FREE DELIVERY</small><em>MORE DETAILS</em></div></div>
  <div class="feature"><span class="ico"><svg width="14" height="14" viewBox="0 0 14 14"><path d="M11 7a4 4 0 1 1-1.2-2.8" fill="none" stroke="#fff" stroke-width="1.6"/><path d="M9 1.5l1.5 3-3.2.5z" fill="#fff"/></svg></span><div><h5>RETURNS</h5><small>30 DAYS</small><em>MORE DETAILS</em></div></div>
  <div class="feature"><span class="ico"><svg width="14" height="14" viewBox="0 0 14 14"><text x="7" y="11" text-anchor="middle" font-family="Open Sans, sans-serif" font-weight="800" font-size="12" fill="#fff">?</text></svg></span><div><h5>QUESTIONS?</h5><small>ASK US</small><em>MORE DETAILS</em></div></div>
  <div class="feature"><span class="ico"><svg width="14" height="14" viewBox="0 0 14 14"><path d="M3 1l2.5 3-1.3 1.5a8 8 0 0 0 4.3 4.3L10 8.5l3 2.5-1.5 2C6 13 1 8 1 2.5z" fill="#fff"/></svg></span><div><h5>LET US HELP</h5><small>CONTACT US</small><em>MORE DETAILS</em></div></div>
</section>

<footer class="footer">
  <div class="about">
    <div class="logo"><span class="mark"></span><span class="name" style="font-weight:800;color:var(--orange)">Furrow Lane Mart</span></div>
    <p>We care about every pet. Browse our range and enjoy fast friendly delivery.</p>
    <div class="cards-pay"><i></i><i></i><i></i><i></i></div>
  </div>
  <div class="col"><h6>QUICK LINKS</h6>Dogs<br>Cats<br>Fish<br>Birds<br>Small Animal</div>
  <div class="col"><h6>SERVICES</h6>Pet Grooming<br>Pet Adoption<br>DIY Dog Wash<br>Pet Hotel<br>Puppy School</div>
  <div class="col"><h6>MY ACCOUNT</h6>Delivery Information<br>Privacy Policy<br>Returns Policy<br>Terms and Conditions<br>FAQs</div>
  <div class="col contact"><h6>CONTACT US</h6>
    <div><svg width="7" height="9" viewBox="0 0 7 9"><path d="M3.5 0a3.5 3.5 0 0 1 3.5 3.5C7 6 3.5 9 3.5 9S0 6 0 3.5A3.5 3.5 0 0 1 3.5 0z" fill="#f7941d"/></svg><span>12 Orchard Row, Maple City</span></div>
    <div><svg width="7" height="9" viewBox="0 0 14 14"><path d="M3 1l2.5 3-1.3 1.5a8 8 0 0 0 4.3 4.3L10 8.5l3 2.5-1.5 2C6 13 1 8 1 2.5z" fill="#f7941d"/></svg><span>1-800-555-0142</span></div>
    <div><svg width="8" height="7" viewBox="0 0 8 7"><rect width="8" height="7" fill="#f7941d"/><path d="M0 0l4 3.5L8 0" fill="none" stroke="#3b2e22" stroke-width=".8"/></svg><span>info@furrowlanemart.com</span></div>
  </div>
</footer>

<div class="bottombar">
  <span>© 2024 Furrow Lane Mart. All rights reserved.</span>
  <div class="social"><i class="dot-ico"></i><i class="dot-ico"></i><i class="dot-ico"></i></div>
</div>
</body>
</html>
```